3 Business Card designs for a company with multiple services

We are a company that has 3 main services:

1) Security - CCTV & Alarm Sepcialists
2) Broadcast - Broadcast Sales and Technical Services
3) Distribution - Quality Products, Quality Service

The broadcast service is for Video Broadcast.

I will include our logos for each service.

I would like to also create a business card design for 7QR in general (see main logo).

Each card will be two-sided. On the front I would think it would include Logo, Name, Posistion and Mobile (and possibly email). And possibly our main number (which may be something like 1800 639 415)

On the back it MUST include a "lined" section to be able to write short quotes / prices.

Then include more details like Phone: 1800 639 415 Fax: 1800 639 417 Postal: PO Box 917, Tallowfield, QLD Australia 4287 Website: www.7qr.com.au

We would like a fresh, inovative card design with that "wow check this out" feel about it.

Look forward to seeing what you can do! :)

Corin

• Quote section on the back!
Editable files.

```html
<!DOCTYPE html>
<html lang="en">
<head>
<meta charset="utf-8">
<title>7QR Security – Business Card Front</title>
<link rel="stylesheet" href="https://fonts.googleapis.com/css2?family=Arimo:wght@400;700&display=swap">
<style>
  :root {
    --red-deep: #a80000;
    --red-mid: #c20d00;
    --red-panel: #c71a00;
    --red-glow: #e0340a;
    --rule: #f0523a;
    --text-white: #ffffff;
    --text-soft: #f3dcd6;
    --mark-grey: #b9b9bb;
  }
  * { margin: 0; padding: 0; box-sizing: border-box; }
  html, body {
    width: 1200px;
    height: 721px;
    overflow: hidden;
    background: var(--red-deep);
  }
  .card {
    position: relative;
    width: 1200px;
    height: 721px;
    overflow: hidden;
    font-family: "Arimo", Arial, sans-serif;
    background:
      radial-gradient(ellipse 70% 80% at 45% 40%, var(--red-mid) 0%, var(--red-deep) 75%);
  }
  .card__panels {
    position: absolute;
    inset: 0;
  }
  .card__burst {
    position: absolute;
    left: 150px;
    top: 130px;
    width: 620px;
    height: 520px;
    border-radius: 50%;
    background: radial-gradient(ellipse at 55% 40%, rgba(224, 52, 10, 0.55) 0%, rgba(200, 20, 0, 0.25) 45%, rgba(168, 0, 0, 0) 72%);
  }
  .brand {
    position: absolute;
    left: 640px;
    top: 263px;
    width: 372px;
    height: 117px;
    display: flex;
    align-items: center;
    gap: 22px;
  }
  .brand__square {
    width: 96px;
    height: 96px;
    background: var(--mark-grey);
    flex: none;
  }
  .brand__name {
    color: var(--text-white);
    font-weight: 700;
    font-size: 40px;
    letter-spacing: 2px;
    white-space: nowrap;
  }
  .contact {
    position: absolute;
    right: 188px;
    top: 460px;
    width: 564px;
    text-align: right;
  }
  .contact__name {
    color: var(--text-white);
    font-size: 33px;
    letter-spacing: -1.2px;
    line-height: 40px;
  }
  .contact__rule {
    height: 2px;
    margin: 12px 0 12px;
    background: linear-gradient(to right, rgba(240, 82, 58, 0.6), var(--rule));
  }
  .contact__line {
    color: var(--text-soft);
    font-size: 22.5px;
    letter-spacing: 1px;
    line-height: 27px;
  }
</style>
</head>
<body>
  <main class="card">
    <div class="card__burst" role="img" aria-label="Abstract glowing red floral swirl artwork"></div>
    <svg class="card__panels" viewBox="0 0 1200 721" aria-hidden="true">
      <defs>
        <filter id="panel-shadow" x="-10%" y="-10%" width="120%" height="130%">
          <feDropShadow dx="0" dy="4" stdDeviation="5" flood-color="#5a0000" flood-opacity="0.45"/>
        </filter>
      </defs>
      <polygon points="48,16 334,375 746,53 460,-306" fill="var(--red-panel)" filter="url(#panel-shadow)"/>
      <polygon points="714,-2 890,218 1172,-2" fill="var(--red-panel)" filter="url(#panel-shadow)"/>
    </svg>

    <div class="brand">
      <span class="brand__square"></span>
      <span class="brand__name">7QR Security</span>
    </div>

    <section class="contact">
      <h1 class="contact__name">LOREM IPSUM DOLOR</h1>
      <div class="contact__rule"></div>
      <p class="contact__line">Manager</p>
      <p class="contact__line">123.4567.890 ||| 1800 639 415</p>
      <p class="contact__line">LoremIpsumDolor@7qr.com</p>
    </section>
  </main>
</body>
</html>
```